Keystonery Billboard - Financial Services Company (Investments, Tax Planning and Insurance)

Our new office has a billboard directly above the office building. We'd like something eye-catching with a strong Call to Action, with the main part of the billboard being under 7 words if possible. We'd like you to include a way to get ahold of us (either our website keystoneryllc.example or our phone number 302-418-2907. You may also include in small font something to indicate that we've been serving the area since 1980 (the DE area, the tri-state area, the Marlowe Hollow, etc.)

We offer financial planning, tax planning, and insurance, and we help our clients to focus on their goals and happiness by providing everything they need for lifelong wealth under one roof.

Our logos are attached, we use a triangle logo with green and gray. We use the tagline "discover lasting prosperity" but this does not need to be included.

Potential ideas we have seen from other financial companies-
- the concept that the driver spends more time looking at billboards than planning for their retirement
-something along the lines of "everything you need for your finances is in this building right here" planning, investments, taxes, insurance"
-don't spend your time worrying about retirement, let us help you plan for it
-are you working for your money, or is it working for you?
- retirement takes planning, we're here to help
- ready to retire? talk to us
- need investment advice?
- need help investing?
- crossing your fingers isn't a retirement plan. we can help.
- retiring soon? you need help.

Those are just general ideas, please feel free to be creative.

brand colors:
#00b585
#00b185
#000000
#ffffff
#6d6f75
#6d6f75
#6f7074
#021712
#052e24

```html
<!DOCTYPE html>
<html lang="en">
<head>
<meta charset="utf-8">
<title>Keystonery Billboard</title>
<link rel="stylesheet" href="https://fonts.googleapis.com/css2?family=Montserrat:wght@500;700;800&display=swap">
<style>
  :root {
    --brand-green: #00a862;
    --brand-gray: #6d6f75;
    --ink-gray: #5f6166;
    --mint-light: #f6fbf8;
    --mint-mid: #d8f1e9;
    --mint-deep: #a9e2d6;
    --white: #ffffff;
    --stage: #e8ebed;
    --photo-top: #4a3a33;
    --photo-mid: #d9d6d0;
    --photo-low: #c4c1bb;
  }
  * { margin: 0; padding: 0; box-sizing: border-box; }
  html, body {
    width: 1200px;
    height: 900px;
    overflow: hidden;
    background: var(--stage);
    font-family: "Montserrat", Arial, sans-serif;
  }
  .billboard {
    position: absolute;
    left: 0;
    top: 200px;
    width: 1200px;
    height: 500px;
    overflow: hidden;
    background: linear-gradient(100deg, var(--mint-light) 0%, var(--mint-mid) 60%, var(--mint-deep) 100%);
  }
  .accent-shapes {
    position: absolute;
    left: 0;
    top: 0;
    width: 1200px;
    height: 500px;
  }
  .brand {
    position: absolute;
    left: 132px;
    top: 52px;
  }
  .brand-name {
    font-weight: 700;
    font-size: 62px;
    line-height: 1;
    color: var(--brand-green);
    letter-spacing: -0.5px;
  }
  .brand-tagline {
    margin-top: 8px;
    font-weight: 500;
    font-size: 12px;
    letter-spacing: 5.2px;
    color: var(--brand-gray);
    text-transform: uppercase;
  }
  .headline {
    position: absolute;
    left: 50px;
    top: 196px;
    font-weight: 800;
    font-size: 62px;
    line-height: 68px;
    color: var(--ink-gray);
    text-transform: uppercase;
    letter-spacing: -0.5px;
  }
  .headline .accent { color: var(--brand-green); }
  .contact-band {
    position: absolute;
    left: 0;
    top: 424px;
    width: 706px;
    height: 76px;
    background: var(--brand-gray);
    clip-path: polygon(0 0, 100% 0, 94% 100%, 0 100%);
    display: flex;
    align-items: center;
    padding-left: 50px;
    color: var(--white);
    font-weight: 800;
  }
  .call-label {
    font-size: 31px;
    letter-spacing: 1.5px;
    margin-right: 30px;
  }
  .phone-icon {
    width: 44px;
    height: 44px;
    margin-right: 12px;
    flex: none;
  }
  .phone-number {
    font-size: 37px;
    letter-spacing: -0.5px;
  }
  .hero-photo {
    position: absolute;
    left: 800px;
    top: 18px;
    width: 210px;
    height: 482px;
    border-radius: 105px 105px 0 0;
    background: linear-gradient(180deg, var(--photo-top) 0%, var(--photo-top) 22%, var(--photo-mid) 42%, var(--photo-low) 100%);
  }
</style>
</head>
<body>
  <main class="billboard">
    <svg class="accent-shapes" viewBox="0 0 1200 500" aria-hidden="true">
      <polygon points="700,500 928,0 1040,0 1105,150 1000,500" fill="#00a862"/>
      <polygon points="1005,500 1130,215 1200,215 1200,500" fill="#6d6f75"/>
    </svg>

    <div class="brand">
      <div class="brand-name">Keystonery</div>
      <div class="brand-tagline">Discover lasting prosperity</div>
    </div>

    <h1 class="headline">
      Worrying about<br>
      your <span class="accent">money?</span><br>
      <span class="accent">Us too!</span>
    </h1>

    <div class="contact-band">
      <span class="call-label">CALL US</span>
      <svg class="phone-icon" viewBox="0 0 44 44" aria-hidden="true">
        <circle cx="22" cy="22" r="21" fill="#ffffff"/>
        <path d="M15.5 11.5c1-.6 2.2-.3 2.8.7l2.2 3.6c.5.9.3 2-.5 2.7l-1.6 1.3c1.2 2.6 3.2 4.7 5.8 5.9l1.3-1.6c.7-.8 1.8-1 2.7-.5l3.6 2.2c1 .6 1.3 1.8.7 2.8l-1.2 2c-.8 1.3-2.4 1.9-3.9 1.5-7.2-2-12.8-7.6-14.8-14.8-.4-1.5.2-3.1 1.5-3.9z" fill="#6d6f75"/>
      </svg>
      <span class="phone-number">302-418-2907</span>
    </div>

    <div class="hero-photo" role="img" aria-label="Photo of a smiling woman in glasses and a light blazer holding a fan of dollar bills"></div>
  </main>
</body>
</html>
```